Design a cool print brochure for an NGO / Give your work a global impact!!

Hi,
I provide a full design brief (below, please scroll) and a mood board (attached) to help you visualize inside my head.. ;-)
I am also available to help and have worked many years in advertising; we will understand each other.
Objective:
To design an A4 folded in two presentation brochure for a non-profit consulting agency called Verdomo.
Verdomo works in sustainability and international development = working with NGO’s, governments and private sector on global issues such as global warming, education for all etc.
Strategy:
This document is a first step in developing a communication strategy. It will be distributed during a major international event called the Brightwater Aid Forum.
Objective:
The double objective of the brochure is:
a) to inform the recipient of what Verdomo is, in the shortest time possible.
b) to showcase relevant projects to demonstrate Verdomo experience and expertise.
Target:
Main target:
Existing Verdomo contacts, such as members of development organizations, NGOs, private sector foundations (CSR), regional networks and other development actors.
NB: the main target already has a certain awareness of Verdomo: we will try to minimize text to maximize visual impact and readability.
Secondary target:
Verdomo will also distribute the brochure to new prospects of interest during the Brightwater Forum.
Timing:
We will need to finalize the design and have the files by June 1st to allow time for print before the event.
Content:
The document should be concise, highly readable (no clutter) and include:
1. text (that we will provide)
and
2. visual elements such as images, shapes and info-graphics (that is you).
NB: Verdomo does not have its own image bank; photos will be provided by you.
Format:
A4 folded in half - 4pp A5 - PORTRAIT FORMAT) with an impactful visual in the front, logo, title and headline (please see examples in the mood board attached).
Design elements:
Verdomo does not have yet a visual identity (please see: http://verdomo.org) so there is room for creativity and no graphic chart to follow.
The sector of consulting in international development is rather conservative but our intention is to be disruptive and create a “Wow” effect. We count on you for that!
Therefore, the design should be “structured”, “organized”, “uncluttered” but also “modern”, “impactful”, “highly visual” (think infographic or mind map to describe our services and projects).
Please, take the time to see the attached presentation: I give you guidelines and examples of what we want and what we like.
We are looking forward to seeing your work and I am available for comments, questions and support.
Thank you.
RK
Target Market(s)
The full brief is in the project description: please, scroll through it.
The target market is : our existing clients base, working in sustainable development (read: NGO and Allied Assembly people)
Industry/Entity Type
Ngo
Font styles to use
Requirements
Must have
- - Design and color elements: please, no black and white. Our company website is in black and white and without graphics; we want the brochure to break away from that and start creating our brand identity; so please, show us colors and desing elements (shapes, backgrounds, etc).
- You have a chance to showcase your talent in terms of visual identity: what lines, forms, layout and colors can you come up with and apply throughout the brochure and serve as the visual identity of Verdomo?
- The structure of the document should be:
- - Front cover: design elements + impacful photo (see mood board example attached) +our logo + this headline: "Collective action for sustainable development and impact"
- - Inside front: a graphic representation of "Our Services": such as core activity in the center circle and satellite circles for the services we offer.
- - Inside back:
- 1. Icons and text boxes for "Our projects"
- 2. A world map of the countries where we have worked. Full list of countries is here:
- http://verdomo.org/experience-1
- - Back cover: our contact + logos of partners.
- Our partners are listed here:
- Please use their original logos (ie, in color).
- The design we will select will serve as a basis for a graphic chart...so more work to come...word to the wise ;)
- Please check out our website verdomo.org to see what we do etc.
Nice to have
- Icons to reflect our services: what icons can you come up with to describe "training services", "building networks" or "program management"?
- I give examples in the mood board.
Should not have
- We are open to creativity and want to generate a "Wow" effect.
- Just note that the sector is rather conservative so flashy colors and cartoon like characters should be avoided. Think "earth, global change, Allied Assembly, climate" without going too green (it's overdone). ;-)
- Make us stand out in the NGO world
- Now you.

```html
<!DOCTYPE html>
<html lang="en">
<head>
<meta charset="utf-8">
<title>Verdomo – Brochure Cover Spread</title>
<link href="https://fonts.googleapis.com/css2?family=Alegreya+Sans+SC:wght@400;500&family=Alegreya+Sans:wght@400;500&family=Montserrat:wght@700&display=swap" rel="stylesheet">
<style>
  :root {
    --navy-deep: #0b1233;
    --navy: #0d1f5c;
    --royal: #1440a8;
    --glow: #2a6fe0;
    --white: #ffffff;
    --partner-text: #b9c6e6;
    --partner-mark: #3f7fd9;
    --map-red: #c8321e;
    --map-orange: #e8892a;
    --map-yellow: #e8c93a;
    --map-blue: #2f8fe0;
    --map-teal: #3fb3c9;
  }
  html, body {
    margin: 0;
    padding: 0;
    width: 1200px;
    height: 848px;
    overflow: hidden;
    background: var(--navy-deep);
  }
  .spread {
    position: relative;
    width: 1200px;
    height: 848px;
    display: flex;
    font-family: "Alegreya Sans", sans-serif;
    color: var(--white);
  }
  .panel {
    position: relative;
    height: 848px;
    overflow: hidden;
  }
  .back-cover {
    width: 596px;
    background:
      radial-gradient(ellipse at 55% 55%, rgba(20, 64, 168, 0.75) 0%, rgba(13, 31, 92, 0.4) 45%, transparent 75%),
      linear-gradient(170deg, #0f2a80 0%, var(--navy) 40%, var(--navy-deep) 85%);
  }
  .fold {
    width: 4px;
    background: #070b1f;
  }
  .front-cover {
    width: 600px;
    background:
      radial-gradient(ellipse at 50% 85%, rgba(42, 111, 224, 0.55) 0%, transparent 60%),
      linear-gradient(180deg, #070c24 0%, var(--navy) 55%, var(--royal) 100%);
  }

  .wordmark {
    position: absolute;
    left: 0;
    right: 0;
    text-align: center;
    font-family: "Alegreya Sans", sans-serif;
    font-weight: 500;
    color: var(--white);
    letter-spacing: 1px;
    margin: 0;
  }
  .back-cover .wordmark { top: 112px; font-size: 62px; left: -10px; }
  .front-cover .wordmark { top: 448px; font-size: 92px; left: 10px; }

  .contact {
    position: absolute;
    top: 196px;
    left: 0;
    width: 596px;
    text-align: center;
    margin: 0;
  }
  .contact-title {
    font-family: "Montserrat", sans-serif;
    font-weight: 700;
    font-size: 22px;
    letter-spacing: -0.5px;
    margin: 0 0 6px 12px;
  }
  .contact-line {
    font-family: "Alegreya Sans SC", sans-serif;
    font-size: 25px;
    letter-spacing: -0.6px;
    margin: 0;
    line-height: 36px;
  }

  .partners-title {
    position: absolute;
    top: 524px;
    left: 0;
    width: 620px;
    text-align: center;
    font-family: "Alegreya Sans SC", sans-serif;
    font-weight: 400;
    font-size: 29px;
    letter-spacing: -1px;
    margin: 0;
  }
  .partner-grid {
    position: absolute;
    left: 18px;
    top: 588px;
    width: 572px;
    list-style: none;
    margin: 0;
    padding: 0;
  }
  .partner {
    position: absolute;
    display: flex;
    align-items: center;
    gap: 7px;
    font-family: "Alegreya Sans SC", sans-serif;
    font-size: 15px;
    color: var(--partner-text);
    white-space: nowrap;
  }
  .partner-mark {
    width: 14px;
    height: 14px;
    flex: none;
    background: var(--partner-mark);
  }
  .partner-mark.round { border-radius: 50%; }
  .partner-badge {
    width: 106px;
    height: 70px;
    background: #0f3aa6;
  }

  .world-map {
    position: absolute;
    top: 0;
    left: 0;
    width: 600px;
    height: 440px;
    background:
      radial-gradient(ellipse at 18% 75%, var(--map-red) 0%, rgba(200, 50, 30, 0.6) 14%, transparent 28%),
      radial-gradient(ellipse at 50% 62%, var(--map-orange) 0%, rgba(232, 201, 58, 0.7) 14%, transparent 30%),
      radial-gradient(ellipse at 88% 62%, var(--map-orange) 0%, transparent 22%),
      radial-gradient(ellipse at 72% 30%, var(--map-teal) 0%, rgba(63, 179, 201, 0.6) 25%, transparent 50%),
      radial-gradient(ellipse at 20% 20%, var(--map-blue) 0%, rgba(47, 143, 224, 0.6) 22%, transparent 42%),
      linear-gradient(180deg, rgba(7, 12, 36, 0.2) 0%, rgba(7, 12, 36, 0.9) 100%);
    -webkit-mask-image: linear-gradient(180deg, #000 70%, transparent 100%);
            mask-image: linear-gradient(180deg, #000 70%, transparent 100%);
  }

  .tagline-lead {
    position: absolute;
    top: 644px;
    left: 0;
    width: 600px;
    text-align: center;
    font-family: "Alegreya Sans SC", sans-serif;
    font-size: 27px;
    letter-spacing: -0.8px;
    margin: 0;
  }
  .tagline-rule {
    position: absolute;
    top: 692px;
    left: 49px;
    width: 501px;
    height: 3px;
    background: var(--white);
  }
  .headline {
    position: absolute;
    top: 700px;
    left: 0;
    width: 600px;
    text-align: center;
    font-family: "Alegreya Sans", sans-serif;
    font-weight: 500;
    font-size: 36px;
    line-height: 37px;
    letter-spacing: 0.3px;
    margin: 0;
    word-spacing: 10px;
  }
</style>
</head>
<body>
<main class="spread">

  <section class="panel back-cover">
    <p class="wordmark">Verdomo</p>

    <address class="contact">
      <p class="contact-title">CONTACT US</p>
      <p class="contact-line">T: +34 611 480 275</p>
      <p class="contact-line">E: info@verdomo.org</p>
    </address>

    <h2 class="partners-title">OUR PARNERS</h2>

    <ul class="partner-grid">
      <li class="partner" style="left:4px; top:36px;"><span class="partner-mark round"></span>Allied Assembly</li>
      <li class="partner" style="left:132px; top:5px;"><span class="partner-badge" role="img" aria-label="Partner badge"></span></li>
      <li class="partner" style="left:258px; top:36px;"><span class="partner-mark round"></span>Climate Circle</li>
      <li class="partner" style="left:410px; top:36px;"><span class="partner-mark"></span>Northgate School</li>

      <li class="partner" style="left:4px; top:110px;"><span class="partner-mark"></span>Cities Network</li>
      <li class="partner" style="left:160px; top:110px;">Halvorsen Foundation</li>
      <li class="partner" style="left:410px; top:110px;"><span class="partner-mark round"></span>Civic Institute</li>

      <li class="partner" style="left:4px; top:190px;"><span class="partner-mark round"></span>Public Policy Fund</li>
      <li class="partner" style="left:190px; top:190px;"><span class="partner-mark"></span>Meridian College</li>
      <li class="partner" style="left:396px; top:190px;">Kessler Cooperation</li>
    </ul>
  </section>

  <div class="fold" aria-hidden="true"></div>

  <section class="panel front-cover">
    <div class="world-map" role="img" aria-label="Painted world map in blues, yellows, oranges and reds showing the continents"></div>

    <h1 class="wordmark">Verdomo</h1>

    <p class="tagline-lead">COLLECTIVE ACTION FOR</p>
    <div class="tagline-rule" aria-hidden="true"></div>
    <p class="headline">SUSTAINABLE DEVELOPMENT<br>AND IMPACT</p>
  </section>

</main>
</body>
</html>
```